Healthcare and Professional IT Services Company need a redesigned business card

We are a IT Services company that targets small medical practices and professional business such as Attorneys, Accounts, Architects etc. We want to communicate a professional yet friendly image using recent logo redesign here on ArtHarbor. Like to see the colors blue and orange in the design. Must use the Tall Pine Computing as displayed in the new logo - then also want to incorporate the fish logo as well.

Target Market(s)

Small medical and professional services

Industry/Entity Type

It Company

Contact Information for Business Card

The usual stuff, place for name address phone website. Also maybe our tagline which is "hooked on technology"

Requirements
Must have
• My new logo and the fish somewhere on the card

```html
<!DOCTYPE html>
<html lang="en">
<head>
<meta charset="utf-8">
<title>Tall Pine Computing – Business Card</title>
<link rel="stylesheet" href="https://fonts.googleapis.com/css2?family=Arimo:wght@400;700&display=swap">
<style>
  :root {
    --backdrop: #e9ecef;
    --card-white: #ffffff;
    --back-sky: #4cc5ea;
    --back-sky-deep: #3fb6e0;
    --wave-light: #4cbfe6;
    --wave-deep: #436fb8;
    --brand-blue: #3b6cb7;
    --text-on-blue: #ffffff;
    --mark-orange: #e9793a;
  }
  * { margin: 0; padding: 0; box-sizing: border-box; }
  html, body {
    width: 1200px;
    height: 902px;
    overflow: hidden;
    background: var(--backdrop);
    font-family: "Arimo", Arial, sans-serif;
  }
  .canvas {
    width: 1200px;
    height: 902px;
    display: flex;
    flex-direction: column;
    align-items: center;
    justify-content: center;
    gap: 30px;
  }
  .card {
    position: relative;
    width: 700px;
    height: 400px;
    overflow: hidden;
    box-shadow: 0 8px 24px rgba(0, 0, 0, 0.16);
  }

  /* Reverse side */
  .card-back {
    background: linear-gradient(160deg, var(--back-sky), var(--back-sky-deep));
    display: flex;
    align-items: center;
    justify-content: center;
  }
  .back-brand {
    font-size: 62px;
    font-weight: 700;
    color: var(--text-on-blue);
    opacity: 0.9;
    letter-spacing: -0.5px;
    white-space: nowrap;
  }

  /* Front side */
  .card-front { background: var(--card-white); }
  .wave {
    position: absolute;
    inset: 0;
    width: 100%;
    height: 100%;
  }
  .wave .band-light { fill: var(--wave-light); }
  .wave .band-deep { fill: var(--wave-deep); }
  .brand-mark {
    position: absolute;
    left: 130px;
    top: 62px;
    width: 76px;
    height: 76px;
    border-radius: 50%;
    background: var(--mark-orange);
  }
  .brand-name {
    position: absolute;
    left: 222px;
    top: 78px;
    font-size: 36px;
    font-weight: 700;
    color: var(--brand-blue);
    letter-spacing: -0.3px;
    white-space: nowrap;
  }
  .holder-name {
    position: absolute;
    left: 48px;
    top: 330px;
    font-size: 23px;
    font-weight: 700;
    color: var(--text-on-blue);
  }
  .contact-divider {
    position: absolute;
    left: 298px;
    top: 274px;
    width: 2px;
    height: 112px;
    background: var(--text-on-blue);
  }
  .contact-list {
    position: absolute;
    left: 310px;
    top: 274px;
    list-style: none;
  }
  .contact-list li {
    display: flex;
    align-items: center;
    gap: 8px;
    height: 28px;
    font-size: 14px;
    color: var(--text-on-blue);
    white-space: nowrap;
  }
  .contact-icon { width: 16px; height: 16px; flex: none; }
  .contact-icon .icon-box { fill: var(--text-on-blue); }
  .contact-icon .icon-mark { fill: none; stroke: var(--wave-deep); stroke-width: 1.6; }
  .contact-icon .icon-fill { fill: var(--wave-deep); }
</style>
</head>
<body>
<main class="canvas">
  <article class="card card-back">
    <p class="back-brand">Tall Pine Computing</p>
  </article>

  <article class="card card-front">
    <svg class="wave" viewBox="0 0 700 400" preserveAspectRatio="none" aria-hidden="true">
      <path class="band-light" d="M0,238 C170,252 320,248 440,188 C560,128 630,120 700,116 L700,400 L0,400 Z"/>
      <path class="band-deep" d="M0,262 C170,276 325,272 448,212 C568,152 635,142 700,138 L700,400 L0,400 Z"/>
    </svg>

    <div class="brand-mark" aria-hidden="true"></div>
    <h1 class="brand-name">Tall Pine Computing</h1>

    <p class="holder-name">Maren Holloway</p>

    <div class="contact-divider"></div>
    <ul class="contact-list">
      <li>
        <svg class="contact-icon" viewBox="0 0 22 22" aria-hidden="true">
          <rect class="icon-box" width="22" height="22" rx="3"/>
          <path class="icon-fill" d="M6,5 l3,0 l1,4 l-2,1.5 c1,2 2.5,3.5 4.5,4.5 l1.5,-2 l4,1 l0,3 c-7,0.5 -12.5,-5 -12,-12 z"/>
        </svg>
        1300 555 014
      </li>
      <li>
        <svg class="contact-icon" viewBox="0 0 22 22" aria-hidden="true">
          <rect class="icon-box" width="22" height="22" rx="3"/>
          <rect class="icon-mark" x="4" y="6" width="14" height="10"/>
          <path class="icon-mark" d="M4,6 L11,12 L18,6"/>
        </svg>
        info@tallpinecomputing.com.au
      </li>
      <li>
        <svg class="contact-icon" viewBox="0 0 22 22" aria-hidden="true">
          <rect class="icon-box" width="22" height="22" rx="3"/>
          <circle class="icon-mark" cx="11" cy="11" r="6.5"/>
          <ellipse class="icon-mark" cx="11" cy="11" rx="3" ry="6.5"/>
          <path class="icon-mark" d="M4.5,11 L17.5,11"/>
        </svg>
        www.tallpinecomputing.com
      </li>
      <li>
        <svg class="contact-icon" viewBox="0 0 22 22" aria-hidden="true">
          <rect class="icon-box" width="22" height="22" rx="3"/>
          <path class="icon-fill" d="M11,4 c-3,0 -5,2.2 -5,5 c0,3.5 5,9 5,9 c0,0 5,-5.5 5,-9 c0,-2.8 -2,-5 -5,-5 z"/>
          <circle class="icon-box" cx="11" cy="9" r="1.8"/>
        </svg>
        2100 W. Cedar Ridge Road Mesa, Arizona 85201
      </li>
    </ul>
  </article>
</main>
</body>
</html>
```